Label Design for Food Brand

We want a modern label for our spice blends. We are completely open in which direction, it should be modern and beautiful.

Use for Sample spice mixture: "Kelvo Dusk"

Here the Packaging:
https://www.merlitrove-example.com/media/xlarge/1700_1.jpg
Abmessung: Ø 54 x 67 mm

Target Market(s)

Food

Industry/Entity Type

Food

Requirements
Must have
• Logo, Name of Flavr
Should not have
• Images of food

```html
<!DOCTYPE html>
<html lang="en">
<head>
<meta charset="utf-8">
<title>Kelvo Dusk – Spice Blend Label</title>
<link rel="stylesheet" href="https://fonts.googleapis.com/css2?family=Mulish:wght@200;300;400;800;900&display=swap">
<style>
  :root {
    --ink: #151515;
    --paper: #ffffff;
    --backdrop: #ececec;
    --band-text: #ffffff;
  }
  * { box-sizing: border-box; margin: 0; padding: 0; }
  html, body {
    width: 1200px;
    height: 750px;
    overflow: hidden;
    background: var(--backdrop);
    font-family: "Mulish", sans-serif;
    color: var(--ink);
  }
  .label {
    position: absolute;
    left: 170px;
    top: 130px;
    width: 860px;
    height: 490px;
    background: var(--ink);
  }
  .brand-band {
    position: absolute;
    left: 0;
    top: 0;
    width: 130px;
    height: 100%;
    display: flex;
    align-items: flex-end;
    justify-content: center;
    padding-bottom: 40px;
  }
  .brand-name {
    writing-mode: vertical-rl;
    transform: rotate(180deg);
    font-weight: 800;
    font-size: 46px;
    letter-spacing: 1px;
    color: var(--band-text);
    line-height: 1;
  }
  .panel {
    position: absolute;
    left: 130px;
    top: 56px;
    right: 0;
    bottom: 56px;
    background: var(--paper);
    padding: 34px 0 0 70px;
  }
  .blend-name {
    line-height: 0.86;
  }
  .blend-name .line-light {
    display: block;
    font-weight: 200;
    font-size: 150px;
    letter-spacing: -2px;
  }
  .blend-name .line-heavy {
    display: block;
    font-weight: 900;
    font-size: 118px;
    letter-spacing: 1px;
    margin-top: 6px;
  }
  .tagline {
    margin-top: 22px;
    font-size: 24px;
    line-height: 1.12;
    font-weight: 300;
    letter-spacing: 0.5px;
    width: 560px;
  }
  .tagline strong { font-weight: 800; }
  .claims {
    margin-top: 10px;
    width: 560px;
    border-top: 4px solid var(--ink);
    display: flex;
  }
  .claim {
    flex: 1;
    font-size: 15px;
    font-weight: 400;
    letter-spacing: 0.5px;
    padding: 14px 0 0 16px;
    height: 44px;
  }
  .claim + .claim { border-left: 4px solid var(--ink); }
  .claim strong { font-weight: 800; }
</style>
</head>
<body>
  <div class="label">
    <div class="brand-band">
      <span class="brand-name">ORVEL PANTRY</span>
    </div>
    <div class="panel">
      <h1 class="blend-name">
        <span class="line-light">KELVO</span>
        <span class="line-heavy">DUSK</span>
      </h1>
      <p class="tagline">HANDCRAFTED WITH <strong>HIGHEST<br>QUALITY INGREDIENTS</strong></p>
      <div class="claims">
        <div class="claim">GLUTEN <strong>FREE</strong></div>
        <div class="claim">NO <strong>MSG</strong></div>
        <div class="claim">NO <strong>SOY</strong></div>
      </div>
    </div>
  </div>
</body>
</html>
```